Larkhollow needs a Webpage Design

We need a webpage for Dr. XYZ who is doing consultancy practice in the area of speech, language, and reading disabilities. He is doing his consultancy practice as "Larkhollow Consultants". Our target market is clients with annual income of $100,000 or more in Chicago area. Our business philosophy is: "...We provide the best evidence-based services/interventions, at an affordable fee, and deal only with clients who seek such services...."

Dr. XYZ's area of research interests are: a) using assistive technology for communication for children with autism, b) early intervention with focus on parent participation, and c) language learning for children birth-to-five years.

He works at a public university whose school color is 'Orange". Home page should show two logos (university and practice). Each page should stand on its own and reflect the content with minimal scrolling. The colors should be subdued (not bright colors) to attract college educated wealthy individuals who are seeking best evidence-based practice in speech, language, and reading for their children.

We need five pages: Home, Consultation, Research, Professional Development, and Contact (with google map directions). The home page should have space for a picture and links for facebook, twitter, and google plus. Other pages should have space for at least one picture and links to pdf files.

The overall design should show healthcare service, evidence-based early intervention with focus on parent participation, and project that we are leaders in the field.

```html
<!DOCTYPE html>
<html lang="en">
<head>
<meta charset="utf-8">
<title>Larkhollow Consultants</title>
<link href="https://fonts.googleapis.com/css2?family=Varela+Round&family=Open+Sans:wght@400;600;700&display=swap" rel="stylesheet">
<style>
:root{
  --sky:#29c5f2;
  --sky-deep:#17b2e6;
  --cta:#38c4ee;
  --navy:#1b5e84;
  --ink:#333;
  --muted:#777;
  --footer:#1c1c1c;
  --footer-bar:#2b2b2b;
  --white:#fff;
}
*{margin:0;padding:0;box-sizing:border-box}
html,body{width:820px;height:1200px;overflow:hidden;background:var(--white)}
body{position:relative;font-family:"Open Sans",Arial,sans-serif;color:var(--ink)}
.display{font-family:"Varela Round","Trebuchet MS",sans-serif;font-weight:400}
.abs{position:absolute}

.site-header{left:0;top:0;width:820px;height:75px;background:linear-gradient(180deg,#2ccdf5,var(--sky-deep))}
.brand{left:72px;top:26px;color:var(--white);font-size:20px;letter-spacing:-.2px}
.nav{top:34px;display:flex;gap:0;color:var(--white);font-size:12.5px}
.nav a{position:absolute;color:var(--white);text-decoration:none;white-space:nowrap}

.hero{left:0;top:75px;width:820px;height:303px;background:linear-gradient(180deg,#fafbfc,#f0f2f4);border-bottom:1px solid #e2e4e6}
.hero-photo{left:326px;top:75px;width:410px;height:303px;background:radial-gradient(ellipse at 60% 45%,#c9d8ea 0%,#dfe7ef 45%,#eef1f4 80%);}
.hero-kicker{left:75px;top:162px;color:var(--navy);font-size:20px}
.hero-title{left:75px;top:188px;color:var(--sky-deep);font-size:27px}
.hero-text{left:79px;top:230px;width:290px;font-size:8.5px;line-height:14px;color:#666}
.dots{left:80px;top:267px;display:flex;gap:3px}
.dots span{width:8px;height:8px;border-radius:50%;background:#b8c4cc}
.dots span:first-child{background:#5c7384}

.intro-title{left:0;width:820px;top:406px;text-align:center;font-size:24px;color:#444}
.intro-sub{left:0;width:820px;top:439px;text-align:center;font-size:14px;color:#444}
.intro-text{left:110px;width:600px;top:468px;text-align:center;font-size:8.5px;line-height:14.5px;color:#777}

.card-photo{top:544px;width:199px;height:94px}
.photo-meeting{left:70px;background:linear-gradient(135deg,#d9c3a8,#e9e5df 50%,#8a98ab)}
.photo-class{left:297px;background:linear-gradient(135deg,#c9a35a,#d98a55 45%,#3d5b4a)}
.card-title{top:649px;font-size:14.5px;color:var(--sky-deep)}
.card-text{top:673px;width:200px;font-size:8.5px;line-height:15px;color:#888}
.learn{top:720px;font-size:10px;color:#333;text-transform:uppercase}

.research-title{left:525px;top:541px;font-size:17px;color:#333}
.research-text{left:526px;top:568px;width:220px;font-size:8.5px;line-height:15px;color:#888}
.research-list{left:527px;top:622px;width:220px;list-style:none;font-size:8.7px;line-height:15px;color:#444}
.research-list li{margin-bottom:7px}
.research-list b{font-weight:400;color:var(--sky-deep)}

.cta{left:0;top:788px;width:820px;height:194px;background:var(--cta)}
.cta-title{left:0;width:820px;top:831px;text-align:center;color:var(--white);font-size:22px}
.cta-text{left:160px;width:500px;top:862px;text-align:center;color:var(--white);font-size:9.2px;line-height:17px}
.cta-button{left:357px;top:908px;width:106px;height:28px;background:#2a2a2a;color:var(--white);font-size:10.5px;font-weight:700;display:flex;align-items:center;justify-content:center;border-radius:2px}

.site-footer{left:0;top:982px;width:820px;height:173px;background:var(--footer)}
.footer-col{top:1010px;color:var(--white)}
.footer-col h4{font-family:"Varela Round",sans-serif;font-weight:400;font-size:14px;margin-bottom:7px}
.footer-col li{list-style:none;font-size:8.5px;font-weight:600;color:#ccc;line-height:16.6px}
.social{display:flex;gap:3px;margin-top:2px}
.social span{width:19px;height:19px;border-radius:50%;background:var(--white)}
.footer-bar{left:0;top:1155px;width:820px;height:45px;background:var(--footer-bar)}
.legal{left:72px;top:1171px;font-size:8px;color:#999}
</style>
</head>
<body>
<header class="abs site-header"></header>
<div class="abs brand display">Larkhollow Consultants</div>
<nav class="abs nav display" style="left:0">
  <a style="left:328px">Home</a>
  <a style="left:381px">Consultation</a>
  <a style="left:471px">Research</a>
  <a style="left:541px">Professional Development</a>
  <a style="left:704px">Contact</a>
</nav>

<section class="abs hero"></section>
<div class="abs hero-photo" role="img" aria-label="Photo of a smiling consultant speaking at a lectern with a microphone"></div>
<div class="abs hero-kicker display">Consultancy Practice in</div>
<div class="abs hero-title display">Speech &amp; Languages</div>
<p class="abs hero-text">Aliquam nec erat at purus cursus interdum Vestibulum ligula augue bibendum accumsan vestibulum commodo</p>
<div class="abs dots"><span></span><span></span><span></span></div>

<h1 class="abs intro-title display">Donec convallis pede venenatis nibh quam</h1>
<h2 class="abs intro-sub display">Pellentesque faucibus accumsan ultricies</h2>
<p class="abs intro-text">Mauris vel lacus vitae felis vestibulum volutpat Etiam est nunc venenatis in tristique eu imperdiet ac nisl Cum sociis natoque penatibus et magnis dis parturient montes nascetur ridiculus mus In iaculis facilisis massa Etiam eu urna Sed porta Suspendisse quam</p>

<div class="abs card-photo photo-meeting" role="img" aria-label="Photo of professionals in a business meeting"></div>
<h3 class="abs card-title display" style="left:71px">Professional Development</h3>
<p class="abs card-text" style="left:72px">Etiam est nunc venenatis in tristique eu imperdiet ac nisl Cum sociis natoque penatibus Ut nisi erat fermentum vel congue id euismod in elit</p>
<a class="abs learn" style="left:72px">Learn More</a>

<div class="abs card-photo photo-class" role="img" aria-label="Photo of a teacher with a group of schoolchildren in a classroom"></div>
<h3 class="abs card-title display" style="left:298px">Consulation &amp; Learning</h3>
<p class="abs card-text" style="left:299px">Etiam est nunc venenatis in tristique eu imperdiet ac nisl Cum sociis natoque penatibus Ut nisi erat fermentum vel congue</p>
<a class="abs learn" style="left:299px">Learn More</a>

<h3 class="abs research-title display">Our Research</h3>
<p class="abs research-text">Etiam est nunc venenatis in tristique eu imperdiet ac nisl Cum sociis natoque penatibus Ut nisi erat fermen-tum vel congue id euismod in elit Fusce ultricies</p>
<ul class="abs research-list">
  <li><b>A)</b> Using assistive technology for communication for children with autism,</li>
  <li><b>B)</b> Early intervention with focus on parent participa-tion</li>
  <li><b>C)</b> Language learning for children birth-to-five years.</li>
</ul>

<section class="abs cta"></section>
<h2 class="abs cta-title display">Do You Want to Join Us Now</h2>
<p class="abs cta-text">Pellentesque faucibus Ut accumsan ultricies elit Maecenas at justo id velit placerat molestie Donec dictum lectus non odio Cras a ante vitae enim iaculis aliquam Mauris nunc</p>
<a class="abs cta-button">CLICK HERE</a>

<footer class="abs site-footer"></footer>
<div class="abs footer-col" style="left:82px"><h4>Company</h4><ul><li>Morbi ornare</li><li>Gravida elit Integer</li><li>Congue augue</li><li>Malesuada</li><li>Dui aliquet</li></ul></div>
<div class="abs footer-col" style="left:212px"><h4>Resources</h4><ul><li>Morbi ornare</li><li>Gravida elit Integer</li><li>Laculis ipsum</li><li>Dui aliquet</li></ul></div>
<div class="abs footer-col" style="left:340px"><h4>Help &amp; Support</h4><ul><li>FAQ</li><li>Stay safe</li><li>Contact us</li></ul></div>
<div class="abs footer-col" style="left:476px"><h4>Get in touch</h4><div class="social"><span></span><span></span><span></span></div></div>
<div class="abs footer-bar"></div>
<div class="abs legal">© 2013 Company Name.&nbsp; All right reserved.&nbsp; Term of Use</div>
</body>
</html>
```